Web Design

We need a website for a company based in Doha Qatar called
Lumara Maid Service.

It is the number one maid cleaning service company, and we have branches all over qatar.

Luxury Cleaning Service Provider.

The color scheme is gold, yellow and black like the logo.

Before they get to the website, there is an intro video.

The website should depict luxury.

Target Market(s)

People who need maids at their houses.

Industry/Entity Type

Cleaning Service

Requirements
Must have
• Luxury, Sleek, Modern

The opening sequence is a video which I already have. Its too big to upload here so I am going to put it on youtube.

After the opening sequence, the home page should have a widescreen photo background and it should change every five seconds, the first background photo should be of qatar westbay skyline. Then the second background should be of maid photos in cleaning positions. Then the third background should be of cleaner photos etc.

We will send you all the tabs and all the content later.

```html
<!DOCTYPE html>
<html lang="en">
<head>
<meta charset="utf-8">
<title>Lumara Maid Service – Intro</title>
<link rel="stylesheet" href="https://fonts.googleapis.com/css2?family=Open+Sans:wght@400;600;700&display=swap">
<style>
  :root{
    --gold:#f6a93b;
    --gold-soft:#f4b54a;
    --brown:#5a2d0c;
    --white:#ffffff;
    --black:#000000;
    --bar:#121110;
    --track:#ffffff;
    --sky-top:#9fc0e6;
    --sky-mid:#c2d6ea;
    --haze:#e4e4dc;
    --city:#a89a80;
    --city-deep:#8f8877;
    --shore:#d9c7a0;
    --water:#c3b79c;
    --water-low:#ddd3bc;
  }
  *{box-sizing:border-box;margin:0;padding:0}
  html,body{width:1200px;height:828px;overflow:hidden;background:var(--white)}
  body{font-family:"Open Sans",Arial,sans-serif;position:relative}
  .top-band{position:absolute;left:0;top:0;width:1200px;height:48px;background:var(--gold)}
  .brand{position:absolute;left:0;top:48px;width:1200px;height:82px;background:var(--white);
    display:flex;align-items:center;justify-content:center;gap:12px}
  .brand-dot{width:18px;height:18px;border-radius:50%;background:var(--gold)}
  .brand-name{font-size:26px;font-weight:600;color:var(--brown);letter-spacing:.5px}
  .intro-video{position:absolute;left:0;top:130px;width:1200px;height:653px;overflow:hidden}
  .skyline-photo{position:absolute;inset:0;
    background:linear-gradient(180deg,
      var(--sky-top) 0%,
      var(--sky-mid) 28%,
      var(--haze) 44%,
      #d6d0c0 48%,
      var(--city) 54%,
      var(--city-deep) 62%,
      var(--shore) 67%,
      var(--water) 72%,
      #b9ad93 80%,
      var(--water-low) 92%,
      #e3dac6 100%)}
  .play-big{position:absolute;left:553px;top:263px;width:94px;height:94px;border-radius:50%;
    background:rgba(240,180,70,.8)}
  .play-big svg{position:absolute;left:37px;top:31px}
  .player-bar{position:absolute;left:114px;top:597px;width:971px;height:41px;background:var(--bar)}
  .player-bar .btn-play{position:absolute;left:16px;top:10px}
  .progress{position:absolute;left:78px;top:17px;width:263px;height:8px;border-radius:4px;background:var(--track);overflow:hidden}
  .progress span{display:block;width:26px;height:100%;background:var(--gold-soft)}
  .time{position:absolute;left:350px;top:10px;color:var(--white);font-size:15px;font-weight:600}
  .mute{position:absolute;left:873px;top:12px}
  .volume{position:absolute;left:894px;top:17px;width:58px;height:8px;border-radius:4px;background:var(--track);overflow:hidden}
  .volume span{display:block;width:26px;height:100%;background:var(--gold-soft)}
  .footer{position:absolute;left:0;top:783px;width:1200px;height:45px;background:var(--black);
    display:flex;align-items:center;justify-content:space-between;padding:0 69px}
  .copyright{color:var(--gold);font-size:12px}
  .skip-intro{color:var(--gold);font-size:17px;font-weight:700;text-decoration:none;display:flex;align-items:center;gap:5px}
</style>
</head>
<body>
  <div class="top-band"></div>
  <header class="brand">
    <span class="brand-dot"></span>
    <span class="brand-name">Lumara Maid Service</span>
  </header>

  <section class="intro-video">
    <div class="skyline-photo" role="img" aria-label="Doha West Bay skyline at sunrise under light clouds, towers reflected in calm bay water"></div>
    <div class="play-big">
      <svg width="32" height="36" viewBox="0 0 32 36"><polygon points="0,0 32,18 0,36" fill="#4a2206"/></svg>
    </div>
    <div class="player-bar">
      <svg class="btn-play" width="22" height="22" viewBox="0 0 22 22"><polygon points="1,0 21,11 1,22" fill="#f4b54a"/></svg>
      <div class="progress"><span></span></div>
      <span class="time">6:20</span>
      <svg class="mute" width="16" height="17" viewBox="0 0 16 17"><polygon points="0,5 5,5 13,0 13,17 5,12 0,12" fill="#fff"/></svg>
      <div class="volume"><span></span></div>
    </div>
  </section>

  <footer class="footer">
    <p class="copyright">COPYRIGHT 2014 © LUMARA MAID SERVICE | &nbsp;ALL RIGHTS RESERVED. PRIVACY POLICY</p>
    <a class="skip-intro" href="#">SKIP INTRO
      <svg width="9" height="14" viewBox="0 0 9 14"><polyline points="1.5,1.5 7,7 1.5,12.5" fill="none" stroke="#f6a93b" stroke-width="2.5"/></svg>
    </a>
  </footer>
</body>
</html>
```